Chimney Service company needs new business card design

We need a updated business card with our new logo added. We provide a full range of chimney services throughout Vermont and New Hampshire. The business card will be one sided and color. Attached is our current business card another document showing all the information we would like on the card.
We dont like a lot of flashy colors.... here is a link to our website to get an idea of our branding www.flueguardianvt.example

Target Market(s)

homeowners

Industry/Entity Type

Business

Contact Information for Business Card

See attached sheet for content.

Font styles to use
Serif
Sans Serif

Requirements
Must have
• all information provided on separate sheet
Should not have
• Additional information that may clogg up design

```html
<!DOCTYPE html>
<html lang="en">
<head>
<meta charset="utf-8">
<title>Flue Guardian business card</title>
<link rel="stylesheet" href="https://fonts.googleapis.com/css2?family=Open+Sans:wght@400;600&family=Rubik:wght@700&display=swap">
<style>
  :root {
    --backdrop: #b9b9b9;
    --card-dark: #2b2b2b;
    --card-light: #f3f3f3;
    --ink: #2a2a2a;
    --ink-soft: #3a3a3a;
    --paper: #f2f2f2;
    --accent: #b3161b;
    --rule: #9a9a9a;
  }
  * { box-sizing: border-box; margin: 0; padding: 0; }
  html, body { width: 1200px; height: 576px; overflow: hidden; }
  body { background: var(--backdrop); position: relative; font-family: "Open Sans", sans-serif; }

  .card { position: absolute; top: 138px; height: 292px; border-radius: 14px; overflow: hidden; }
  .card--back { left: 82px; width: 484px; background: var(--card-dark); }
  .card--front { left: 602px; width: 482px; background: var(--card-light); color: var(--ink); }

  .brand { position: absolute; display: flex; align-items: center; gap: 12px; white-space: nowrap; }
  .brand-dot { flex: none; border-radius: 50%; background: currentColor; }
  .brand-name { font-family: "Open Sans", sans-serif; font-weight: 600; letter-spacing: 1.5px; }

  /* back */
  .card--back .brand { left: 0; right: 0; top: 128px; justify-content: center; color: var(--paper); }
  .card--back .brand-dot { width: 16px; height: 16px; }
  .card--back .brand-name { font-size: 27px; }

  /* front */
  .card--front .brand { left: 42px; top: 46px; color: var(--ink); }
  .card--front .brand-dot { width: 18px; height: 18px; }
  .card--front .brand-name { font-size: 28px; }

  .services { position: absolute; right: 236px; top: 134px; list-style: none; text-align: right; font-size: 12.5px; line-height: 20.4px; color: var(--ink-soft); }
  .services li::after { content: ""; display: inline-block; width: 6px; height: 8px; margin-left: 7px; background: var(--accent); border-radius: 50% 50% 40% 40%; }

  .divider { position: absolute; left: 248px; top: 134px; width: 1px; height: 100px; background: var(--rule); }

  .region { position: absolute; left: 262px; top: 132px; width: 168px; }
  .region h2 { font-family: "Rubik", sans-serif; font-weight: 700; font-size: 16.5px; line-height: 19px; color: var(--ink); }
  .since { display: flex; align-items: center; gap: 6px; margin-top: 3px; font-size: 8.5px; color: var(--ink); white-space: nowrap; }
  .since::before, .since::after { content: ""; height: 1px; background: var(--accent); flex: 1; }

  .contact { position: absolute; left: 262px; top: 192px; list-style: none; font-size: 12px; line-height: 15.5px; color: var(--ink-soft); }
  .contact li { display: flex; align-items: center; gap: 10px; }
  .contact svg { width: 10px; height: 10px; fill: var(--accent); }
  .contact .accent { color: var(--accent); }

  .base-rule { position: absolute; left: 22px; right: 22px; top: 259px; height: 1px; background: var(--rule); }
  .footer { position: absolute; left: 0; right: 0; top: 265px; text-align: center; font-size: 11.5px; color: var(--ink-soft); }
  .footer .sep { color: var(--accent); margin: 0 12px; }
</style>
</head>
<body>
  <section class="card card--back" aria-label="Card back">
    <div class="brand"><span class="brand-dot"></span><span class="brand-name">FLUE GUARDIAN</span></div>
  </section>

  <section class="card card--front" aria-label="Card front">
    <div class="brand"><span class="brand-dot"></span><span class="brand-name">FLUE GUARDIAN</span></div>

    <ul class="services">
      <li>Full Masonry Services</li>
      <li>Historic chimney restoration</li>
      <li>Stainless steel liners</li>
      <li>New Chimney installations</li>
      <li>HSCA Certified Chimney sweeps</li>
    </ul>

    <span class="divider"></span>

    <div class="region">
      <h2>SERVING VT AND<br>NEW HAMPSHIRE</h2>
      <div class="since">SINCE 1989</div>
    </div>

    <ul class="contact">
      <li><svg viewBox="0 0 10 10"><path d="M1 3c0-2 2-2 4-2s4 0 4 2v1H7V3H3v1H1zM2 5h6l1 4H1z"/></svg>802-555-0147</li>
      <li><svg viewBox="0 0 10 10"><path d="M0 2h10v6H0z M0 2l5 3 5-3" stroke="#f3f3f3" stroke-width="0.8"/></svg>info@flueguardianvt.example</li>
      <li><svg viewBox="0 0 10 10"><circle cx="5" cy="5" r="4.5"/><path d="M0.5 5h9M5 0.5v9" stroke="#f3f3f3" stroke-width="0.8"/></svg><span>www.<span class="accent">flueguardianvt</span>.example</span></li>
    </ul>

    <span class="base-rule"></span>
    <p class="footer">Fully Insured – Free Estimates<span class="sep">|</span>Family Owned &amp; Operated</p>
  </section>
</body>
</html>
```